Puffy Clouds Cotton Candy

Looking for a logo design and business cards to help a 13 year old entrepreneur promote her cotton candy business.
Contact Information for Business Card
Name, Phone & Email
Colors
E54698
E96AAD
F1A4CE
F9D9EA
FCEFF6
A7469A
B969AE
D3A5CF
EDDBEB
F8F0F9
6B429C
8869AF
B7A5CE
E3DAEB
F3F0F8
Requirements
Must have
- A fun feel that is appropriate for a teenage girl selling cotton candy

```html
<!DOCTYPE html>
<html lang="en">
<head>
<meta charset="utf-8">
<title>Puffy Clouds Cotton Candy – Business Cards</title>
<link rel="stylesheet" href="https://fonts.googleapis.com/css2?family=Montserrat:wght@700&family=Questrial&display=swap">
<style>
  :root {
    --pink: #e54698;
    --purple: #6b429c;
    --purple-text: #5b3a8e;
    --white: #ffffff;
    --rule: #d9d9d9;
    --backdrop: #d4d4d4;
    --card-edge: #e54698;
  }
  * { box-sizing: border-box; margin: 0; padding: 0; }
  html, body {
    width: 1200px;
    height: 800px;
    overflow: hidden;
    background: var(--backdrop);
  }
  .sheet {
    position: relative;
    width: 1200px;
    height: 800px;
    display: flex;
    align-items: center;
    justify-content: center;
    gap: 40px;
  }
  .card {
    position: relative;
    width: 540px;
    height: 309px;
    border-bottom: 3px solid var(--card-edge);
    box-shadow: 0 10px 24px rgba(0,0,0,0.18);
  }

  /* Front: white contact side */
  .card--front {
    background: var(--white);
    display: flex;
    align-items: center;
  }
  .brand {
    display: flex;
    align-items: center;
    gap: 14px;
    width: 270px;
    padding-left: 36px;
  }
  .brand__dot {
    flex: none;
    width: 34px;
    height: 34px;
    border-radius: 50%;
    background: var(--purple);
  }
  .brand__name {
    font-family: "Montserrat", sans-serif;
    font-weight: 700;
    color: var(--pink);
    line-height: 1.1;
  }
  .card--front .brand__name { font-size: 24px; }
  .divider {
    width: 1px;
    height: 90px;
    background: var(--rule);
  }
  .contact {
    padding-left: 26px;
    font-family: "Questrial", sans-serif;
    color: var(--purple-text);
  }
  .contact__name {
    font-family: "Montserrat", sans-serif;
    font-weight: 700;
    font-size: 22px;
    color: var(--pink);
    line-height: 1.1;
  }
  .contact__role {
    font-size: 15px;
    margin-bottom: 12px;
  }
  .contact__line {
    display: flex;
    align-items: center;
    gap: 8px;
    font-size: 14px;
    line-height: 1.5;
  }
  .contact__icon { width: 14px; height: 14px; flex: none; }

  /* Back: purple brand side */
  .card--back {
    background: var(--purple);
    display: flex;
    align-items: center;
    justify-content: center;
  }
  .card--back .brand {
    width: auto;
    padding: 0;
    gap: 18px;
  }
  .card--back .brand__dot {
    width: 52px;
    height: 52px;
    background: var(--white);
  }
  .card--back .brand__name { font-size: 34px; }
</style>
</head>
<body>
<main class="sheet">
  <section class="card card--front" aria-label="Business card front">
    <div class="brand">
      <span class="brand__dot"></span>
      <p class="brand__name">Puffy Clouds<br>Cotton Candy</p>
    </div>
    <span class="divider"></span>
    <div class="contact">
      <p class="contact__name">Marlowe Kinsey</p>
      <p class="contact__role">Managing Director</p>
      <p class="contact__line">
        <svg class="contact__icon" viewBox="0 0 24 24" aria-hidden="true"><path fill="#e54698" d="M6.6 10.8a15.1 15.1 0 0 0 6.6 6.6l2.2-2.2a1 1 0 0 1 1-.25 11.4 11.4 0 0 0 3.6.57 1 1 0 0 1 1 1V20a1 1 0 0 1-1 1A17 17 0 0 1 3 4a1 1 0 0 1 1-1h3.5a1 1 0 0 1 1 1c0 1.25.2 2.45.57 3.57a1 1 0 0 1-.25 1z"/></svg>
        055-318 642 907
      </p>
      <p class="contact__line">
        <svg class="contact__icon" viewBox="0 0 24 24" aria-hidden="true"><rect x="2" y="5" width="20" height="14" rx="1.5" fill="#e54698"/><path d="M3 6.5l9 6.5 9-6.5" fill="none" stroke="#ffffff" stroke-width="1.6"/></svg>
        hello@puffyclouds.com
      </p>
    </div>
  </section>

  <section class="card card--back" aria-label="Business card back">
    <div class="brand">
      <span class="brand__dot"></span>
      <p class="brand__name">Puffy Clouds<br>Cotton Candy</p>
    </div>
  </section>
</main>
</body>
</html>
```